Lanternfield Drinks business cards

We need a business card design for our new logo. The company is modern, progressive, professional, yet approachable. The key products are ready to drink bottles and cans of coffee based beverages.
These cards will be a critical part of the first impression made by our sales organization, business development team, and all external facing personnel.
Card can be a vertical or horizontal orientation.

Target Market(s)

Customers, suppliers, business partners

Industry/Entity Type

Business

Contact Information for Business Card

Business cards should feature Company Name and Logo.

Font styles to use
Serif

Colors

Designer to choose colors to be used in the design.

Requirements
Must have
• Strong readability of Name, phone #, mobile number and email address.
• Job title, website url, Street Address, and other details can be secondary level readability.
Nice to have
• High impact, simplistic quality design.
• Ok to utilize the 'H in the box' separate from the company name

```html
<!DOCTYPE html>
<html lang="en">
<head>
<meta charset="utf-8">
<title>Lanternfield Drinks – Business Cards</title>
<link href="https://fonts.googleapis.com/css2?family=Libre+Baskerville:wght@400;700&display=swap" rel="stylesheet">
<style>
  :root {
    --bg: #9a9a9a;
    --orange: #ee5a2c;
    --orange-deep: #d94a22;
    --white: #ffffff;
    --paper: #f4f4f4;
    --ink: #2b2b2b;
    --gold: #c9892b;
  }
  * { box-sizing: border-box; margin: 0; padding: 0; }
  html, body { width: 1200px; height: 900px; overflow: hidden; }
  body {
    background: radial-gradient(circle at 50% 40%, #a8a8a8, var(--bg) 70%, #858585);
    font-family: "Libre Baskerville", Georgia, serif;
    position: relative;
  }
  .card {
    position: absolute;
    width: 540px;
    height: 309px;
    border-radius: 16px;
    overflow: hidden;
    box-shadow: 0 14px 30px rgba(0,0,0,0.28);
  }
  /* front */
  .card-front {
    left: 70px; top: 110px;
    background: linear-gradient(135deg, var(--orange-deep), var(--orange) 60%, #f26a3c);
    color: var(--white);
    display: flex; flex-direction: column; align-items: center; justify-content: center;
  }
  .brand { display: flex; align-items: center; gap: 14px; }
  .brand-square {
    width: 44px; height: 44px;
    border: 3px solid currentColor;
  }
  .brand-name {
    font-weight: 700; font-size: 26px; letter-spacing: 1px; text-transform: uppercase;
  }
  .card-front .url { margin-top: 48px; font-size: 13px; letter-spacing: 0.3px; }

  /* back */
  .card-back {
    left: 590px; top: 480px;
    background: linear-gradient(180deg, var(--white), var(--paper));
    color: var(--ink);
  }
  .back-brand {
    position: absolute; left: 30px; top: 70px; width: 210px;
    display: flex; flex-direction: column; align-items: center; gap: 12px;
    color: var(--orange);
  }
  .back-brand .brand-square { width: 50px; height: 50px; }
  .back-brand .brand-name { font-size: 20px; text-align: center; line-height: 1.2; }
  .divider {
    position: absolute; left: 252px; top: 48px; width: 1.5px; height: 140px;
    background: var(--orange);
  }
  .contact { position: absolute; left: 274px; top: 44px; }
  .person-name { color: var(--orange); font-weight: 700; font-size: 24px; }
  .person-title { font-size: 15px; margin-top: 2px; margin-bottom: 14px; }
  .contact-list { list-style: none; font-size: 12px; }
  .contact-list li { display: flex; align-items: center; gap: 8px; margin-bottom: 7px; }
  .contact-list svg { width: 12px; height: 12px; fill: var(--orange); flex: none; }
  .address-band {
    position: absolute; left: 0; right: 0; top: 216px; height: 40px;
    background: var(--orange); color: var(--white);
    display: flex; align-items: center; justify-content: center;
    font-size: 13px;
  }
  .bottom-strip {
    position: absolute; left: 0; right: 0; top: 262px; height: 30px;
    background: var(--orange-deep);
  }
</style>
</head>
<body>
  <section class="card card-front">
    <div class="brand">
      <span class="brand-square"></span>
      <span class="brand-name">Lanternfield Drinks</span>
    </div>
    <p class="url">www.lanternfielddrinks.com</p>
  </section>

  <section class="card card-back">
    <div class="back-brand">
      <span class="brand-square"></span>
      <span class="brand-name">Lanternfield Drinks</span>
    </div>
    <div class="divider"></div>
    <div class="contact">
      <h1 class="person-name">Daniel Marsh</h1>
      <p class="person-title">President</p>
      <ul class="contact-list">
        <li>
          <svg viewBox="0 0 24 24" aria-hidden="true"><path d="M6.6 10.8a15 15 0 0 0 6.6 6.6l2.2-2.2a1 1 0 0 1 1-.25 11.4 11.4 0 0 0 3.6.57 1 1 0 0 1 1 1V20a1 1 0 0 1-1 1A17 17 0 0 1 3 4a1 1 0 0 1 1-1h3.5a1 1 0 0 1 1 1c0 1.25.2 2.45.57 3.6a1 1 0 0 1-.25 1z"/></svg>
          555 204 3187
        </li>
        <li>
          <svg viewBox="0 0 24 24" aria-hidden="true"><path d="M2 5h20v14H2z M2 5l10 8 10-8" stroke="#fff" stroke-width="1.5"/></svg>
          info@lanternfielddrinks.com
        </li>
        <li>
          <svg viewBox="0 0 24 24" aria-hidden="true"><circle cx="12" cy="12" r="10"/><path d="M2 12h20M12 2c3 3 3 17 0 20M12 2c-3 3-3 17 0 20" stroke="#fff" stroke-width="1.3" fill="none"/></svg>
          www.lanternfielddrinks.com
        </li>
      </ul>
    </div>
    <div class="address-band">Level 2, 17 Harbour Lane, Eastbrook, VIC 3011</div>
    <div class="bottom-strip"></div>
  </section>
</body>
</html>
```